Website design for legal tech start up in Switzerland (B2B)

We are for a legal tech start up in Switzerland called KOVA. We have been running since August 2016. This will be our first live website.

We need a website designed and business card design for our start-up in Switzerland. We also need the Web design to be converted into HTML and CSS files.

Function of website:
• To inform potential customers of our services
• Form a key part of our digital marketing and sales footprint.
• Branding

Please find attached logo.
Updates

Project Deadline Extended Reason: Giving us time to review submissions and provide opportunity for more submissions. Added Thursday, February 16, 2017

Project Deadline Extended
Reason: Looking for more idea's not necessarily set on blue and grey colours only.

Target Market(s)

B2B tech powered legal services.

Industry/Entity Type

Legal

Contact Information for Business Card

Lean and slick design.

Coding

Coded - Design and coding required

Number of Pages Required

5+ page

Requirements
Must have
• VERY LEAN AND CLEAN DESIGN!
• We have received many great standard designs, but we are looking for something more out-of-the box: You can get inspiration from these designs: http://www.pixelvane.com/websites/clean/
• Thanks!!
• Easy content management system
• Well structured coding for additional development
• Responsive webpage for all types of devices
• SEO optimized
• Tabs (Home, services, team, careers, blog, contact us)
• Colour scheme complementary to logo
Nice to have
• Look and Design - Approachable, High-tech, Modern
• Easy to add chat bot capability in future
Should not have
• Too busy/ too much clutter
• Not take to long to load

```html
<!DOCTYPE html>
<html lang="en">
<head>
<meta charset="utf-8">
<title>KOVA – Legal Advisor</title>
<link href="https://fonts.googleapis.com/css2?family=Lato:wght@300;400;700;900&display=swap" rel="stylesheet">
<style>
:root{
  --navy:#1b3a6b;
  --navy-dark:#13294d;
  --ink:#222a36;
  --text:#4a4f57;
  --muted:#7a8088;
  --line:#d9dce1;
  --card:#ececec;
  --white:#ffffff;
  --footer:#1a1f2b;
}
*{box-sizing:border-box;margin:0;padding:0}
html,body{width:1200px;height:4580px;overflow:hidden}
body{font-family:"Lato",Arial,sans-serif;color:var(--text);background:var(--white);position:relative}
section,header,footer{position:absolute;left:0;width:1200px}
.photo{position:absolute}

/* header */
.site-header{top:0;height:73px;background:var(--white);display:flex;align-items:center;justify-content:space-between;padding:0 80px}
.brand{font-weight:900;font-size:40px;letter-spacing:3px;color:var(--ink)}
.header-right{display:flex;align-items:center;gap:40px}
.header-phone{display:flex;align-items:center;gap:10px;font-size:24px;font-weight:700;color:var(--ink)}
.icon-circle{width:34px;height:34px;border-radius:50%;background:var(--ink);display:flex;align-items:center;justify-content:center}
.menu-btn{width:44px;height:40px;background:var(--ink);border-radius:3px;display:flex;flex-direction:column;justify-content:center;gap:6px;padding:0 10px}
.menu-btn span{height:3px;background:var(--white)}

/* hero */
.hero{top:73px;height:527px}
.hero .photo{inset:0;background:linear-gradient(100deg,#1d2a44 0%,#2b3f64 40%,#6a86b4 70%,#c5b5c8 100%)}
.hero-text{position:absolute;left:80px;top:215px;color:var(--white)}
.hero-title{font-size:40px;font-weight:400;line-height:52px;letter-spacing:1px}
.btn-outline{display:inline-block;margin-top:30px;border:2px solid var(--white);padding:14px 22px;font-size:20px;color:var(--white);background:rgba(19,41,77,.7)}

/* headings */
.section-title{text-align:center;font-size:40px;font-weight:400;color:var(--ink);letter-spacing:1px}
.section-title b{font-weight:900}
.title-rule{width:100px;height:3px;background:var(--ink);margin:14px auto 0}
.title-divider{display:flex;align-items:center;justify-content:center;gap:14px;margin-top:16px}
.title-divider span{width:140px;height:1px;background:var(--muted)}
.title-divider i{width:10px;height:10px;border:2px solid var(--muted);transform:rotate(45deg)}

/* about */
.about{top:600px;height:440px}
.about .section-title{margin-top:40px}
.about-copy{width:1060px;margin:40px auto 0;text-align:center;font-size:15px;line-height:26px}
.about-cards{position:absolute;top:300px;left:180px;display:flex;gap:85px}
.info-card{width:375px;height:110px;background:var(--white);box-shadow:4px 6px 10px rgba(0,0,0,.25);display:flex;gap:18px;padding:20px}
.info-icon{width:70px;height:70px;background:var(--navy);flex:none;display:flex;align-items:center;justify-content:center}
.info-card h3{font-size:18px;color:var(--ink);font-weight:700;margin-bottom:6px}
.info-card p{font-size:13px;line-height:17px;color:var(--muted)}

/* advice band */
.advice{top:1075px;height:372px}
.advice .photo{inset:0;background:linear-gradient(90deg,#3b3d42,#9a9ca0 45%,#b5b6b8 60%,#55575c)}
.advice-box{position:absolute;left:385px;top:70px;width:415px;height:240px;background:rgba(27,58,107,.88);color:var(--white);padding:24px 40px}
.advice-box h2{font-size:28px;font-weight:400;letter-spacing:1px;margin-bottom:20px}
.advice-row{display:flex;align-items:center;gap:20px;font-size:22px}
.advice-or{font-size:22px;font-weight:700;margin:4px 0 8px 75px}
.advice-row small{display:block;font-size:13px;opacity:.8}
.advice-row strong{font-size:28px;font-weight:700}
.white-circle{width:52px;height:52px;border-radius:50%;background:var(--white);display:flex;align-items:center;justify-content:center;flex:none}

/* services */
.services{top:1447px;height:828px}
.services .section-title{margin-top:40px}
.services-copy{width:1060px;margin:36px auto 0;text-align:center;font-size:15px;line-height:26px}
.services-copy a{color:var(--ink);font-weight:700}
.service-grid{position:absolute;top:232px;left:115px;display:grid;grid-template-columns:repeat(3,295px);gap:50px 45px}
.service-card{height:260px;background:var(--card);text-align:center;padding-top:32px;position:relative;border-bottom:3px solid var(--ink)}
.service-card.active{background:var(--navy);color:var(--white)}
.service-icon{width:76px;height:76px;margin:0 auto;background:var(--navy);display:flex;align-items:center;justify-content:center;border:6px solid #d0d3d8}
.service-card h3{font-size:19px;font-weight:400;color:var(--navy);margin-top:34px}
.service-card.active h3{color:var(--white)}
.service-card p{font-size:14px;line-height:20px;margin:10px 40px 0}
.plus{position:absolute;bottom:-3px;left:50%;transform:translateX(-50%);width:36px;height:18px;border-radius:18px 18px 0 0;background:var(--ink);color:var(--white);font-size:18px;line-height:20px}

/* banner with box */
.banner{height:355px}
.banner .photo{inset:0}
.banner-box{position:absolute;left:385px;width:430px;background:rgba(27,58,107,.85);color:var(--white);text-align:center;padding:24px 30px}
.banner-box h2{font-size:30px;font-weight:400;letter-spacing:1px;margin-bottom:14px}
.banner-box p{font-size:14px;line-height:20px}
.team-banner{top:2311px}
.team-banner .photo{background:linear-gradient(180deg,#0f1a2e,#3a5680 55%,#1c2a44)}
.team-banner .banner-box{top:90px}

/* team */
.team{top:2665px;height:295px}
.team-list{display:flex;gap:40px;justify-content:center;margin-top:34px}
.member{width:180px;text-align:center}
.member-photo{width:180px;height:170px;border:5px solid var(--white);box-shadow:0 0 0 1px var(--line),2px 3px 8px rgba(0,0,0,.2);background:linear-gradient(180deg,#5a5f68,#2e323a)}
.member h3{font-size:20px;font-weight:400;color:var(--ink);margin-top:14px}
.member-links{display:flex;justify-content:center;gap:8px;margin-top:12px}
.member-links span{width:28px;height:28px;border-radius:50%;border:1px solid var(--line);display:flex;align-items:center;justify-content:center}

.blog-banner{top:3000px}
.blog-banner .photo{background:linear-gradient(180deg,#3c5a88,#253f66 50%,#14213a)}
.blog-banner .banner-box{top:80px;height:175px}

/* blog */
.blog{top:3355px;height:455px}
.post-list{display:flex;gap:25px;justify-content:center;margin-top:40px}
.post{width:330px;height:335px;background:var(--white);box-shadow:0 1px 6px rgba(0,0,0,.2)}
.post-img{height:180px}
.post-body{display:flex;gap:14px;padding:20px 16px}
.post-date{width:40px;height:44px;background:var(--navy);color:var(--white);text-align:center;font-size:15px;font-weight:700;line-height:22px;flex:none}
.post-date small{display:block;font-size:10px;line-height:14px;background:var(--white);color:var(--navy);border:1px solid var(--navy)}
.post h3{font-size:16px;font-weight:400;color:var(--ink)}
.post .meta{font-size:13px;color:var(--muted);margin:6px 0}
.post p{font-size:13px;line-height:19px;color:var(--muted)}
.dots{display:flex;justify-content:center;gap:8px;margin-top:34px}
.dots span{width:10px;height:10px;border-radius:50%;border:1px solid var(--navy)}
.dots span:first-child{background:var(--navy)}

/* call back */
.callback{top:3810px;height:290px;background:var(--navy);color:var(--white)}
.callback h2{position:absolute;left:88px;top:48px;font-size:40px;font-weight:400;line-height:46px}
.callback-copy{position:absolute;left:88px;top:160px;width:330px;font-size:14px;line-height:20px}
.callback-form{position:absolute;left:458px;top:50px;width:665px}
.callback-form h3{font-size:17px;font-weight:700;margin-bottom:16px}
.form-grid{display:grid;grid-template-columns:1fr 1fr;gap:16px 30px}
.field{height:46px;background:var(--white);color:var(--muted);font-size:14px;padding:14px}
.btn-submit{display:inline-block;margin-top:16px;background:var(--footer);color:var(--white);font-size:18px;letter-spacing:2px;padding:12px 22px}

/* footer */
.site-footer{top:4100px;height:418px;background:linear-gradient(180deg,#161b27,#232b3c 60%,#3a3f4d);color:var(--white);text-align:center}
.contact-row{display:flex;justify-content:space-between;padding:48px 80px 0}
.contact-item{width:300px;font-size:14px}
.contact-item .ico{height:40px;display:flex;align-items:center;justify-content:center;margin-bottom:12px;position:relative}
.contact-item .ico::before,.contact-item .ico::after{content:"";position:absolute;top:50%;width:100px;height:1px;background:rgba(255,255,255,.4)}
.contact-item .ico::before{left:20px}.contact-item .ico::after{right:20px}
.footer-brand{font-size:60px;font-weight:900;letter-spacing:4px;margin-top:36px}
.footer-copy{width:560px;margin:12px auto 0;font-size:14px;line-height:20px;opacity:.85}
.hours{display:flex;justify-content:center;gap:20px;margin-top:22px;font-size:13px;font-weight:700}
.hours span{background:rgba(0,0,0,.55);padding:6px 12px}
.btn-contact{display:inline-block;margin-top:18px;border:1px solid var(--white);padding:8px 14px;font-size:14px;letter-spacing:1px}
.copyright{top:4518px;height:62px;background:var(--footer);color:var(--white);display:flex;align-items:center;justify-content:space-between;padding:0 88px;font-size:15px}
.social{display:flex;gap:12px}
.social span{width:38px;height:38px;border-radius:50%;background:#2f5aa6}
</style>
</head>
<body>

<header class="site-header">
  <div class="brand">KOVA</div>
  <div class="header-right">
    <div class="header-phone">
      <span class="icon-circle"><svg width="18" height="18" viewBox="0 0 24 24"><path fill="#fff" d="M6.6 10.8a15 15 0 0 0 6.6 6.6l2.2-2.2c.3-.3.7-.4 1-.2 1.1.4 2.3.6 3.6.6.6 0 1 .4 1 1V20c0 .6-.4 1-1 1A17 17 0 0 1 3 4c0-.6.4-1 1-1h3.5c.6 0 1 .4 1 1 0 1.2.2 2.4.6 3.6.1.3 0 .7-.2 1z"/></svg></span>
      +41 44 555 0190
    </div>
    <div class="menu-btn"><span></span><span></span><span></span></div>
  </div>
</header>

<section class="hero">
  <div class="photo" role="img" aria-label="City skyline of office towers at dusk"></div>
  <div class="hero-text">
    <h1 class="hero-title">WE ARE EXPERT IN<br>LEGAL ADVISOR</h1>
    <a class="btn-outline">GET A FREE CONSULTATION</a>
  </div>
</section>

<section class="about">
  <h2 class="section-title">ABOUT <b>KOVA</b></h2>
  <div class="title-rule"></div>
  <p class="about-copy">eaque ipsa quae ab illo inventore veritatis et quasi architecto beatae vitae dicta sunt explicabo sed ut perspiciatis unde omnis iste natus error sit voluptatem accusantium doloremque laudantium, totam rem aperiam, eaque ipsa quae ab illo inventore veritatis et quasi architecto beatae vitae dicta sunt explicabo sed ut perspiciatis unde omnis iste natus error sit voluptatem accusantium doloremque eaque ipsa quae ab illo inventore veritatis et quasi architecto beatae vitae dicta sunt explicabo eaque ipsa quae ab illo inventore veritatis et quasi architecto beatae vitae dicta sunt explicabo sed ut perspiciatis unde omnis iste natus error sit voluptatem accusantium doloremque laudantium, totam rem aperiam.</p>
  <div class="about-cards">
    <div class="info-card">
      <div class="info-icon"><svg width="38" height="30" viewBox="0 0 38 30"><circle cx="19" cy="8" r="6" fill="#fff"/><circle cx="7" cy="11" r="4" fill="#fff"/><circle cx="31" cy="11" r="4" fill="#fff"/><path d="M9 28c0-7 4-11 10-11s10 4 10 11z M0 27c0-5 3-8 7-8 2 0 3 .5 4 1.5-2 2-3 4-3 6.5z M38 27c0-5-3-8-7-8-2 0-3 .5-4 1.5 2 2 3 4 3 6.5z" fill="#fff"/></svg></div>
      <div><h3>Our Mission</h3><p>Sed ut perspiciatis unde omnis iste natus error sit voluptatem accusantium Sed ut perspiciatis unde omnis.</p></div>
    </div>
    <div class="info-card">
      <div class="info-icon"><svg width="36" height="36" viewBox="0 0 36 36"><circle cx="18" cy="18" r="15" fill="none" stroke="#fff" stroke-width="3"/><circle cx="18" cy="18" r="8" fill="none" stroke="#fff" stroke-width="3"/><circle cx="18" cy="18" r="2.5" fill="#fff"/><path d="M18 18 32 4" stroke="#fff" stroke-width="3"/></svg></div>
      <div><h3>Our Vision</h3><p>Sed ut perspiciatis unde omnis iste natus error sit voluptatem accusantium Sed ut perspiciatis unde omnis.</p></div>
    </div>
  </div>
</section>

<section class="advice">
  <div class="photo" role="img" aria-label="Two business people shaking hands across a desk"></div>
  <div class="advice-box">
    <h2>NEED A LEGAL ADVICE ?</h2>
    <div class="advice-row">
      <span class="white-circle"><svg width="26" height="26" viewBox="0 0 26 26"><circle cx="13" cy="8" r="6" fill="#1b3a6b"/><path d="M2 25c0-7 5-10 11-10s11 3 11 10z" fill="#1b3a6b"/></svg></span>
      Get A FREE CONSULTATION
    </div>
    <div class="advice-or">OR</div>
    <div class="advice-row">
      <span class="white-circle"><svg width="24" height="24" viewBox="0 0 24 24"><path fill="#1b3a6b" d="M6.6 10.8a15 15 0 0 0 6.6 6.6l2.2-2.2c.3-.3.7-.4 1-.2 1.1.4 2.3.6 3.6.6.6 0 1 .4 1 1V20c0 .6-.4 1-1 1A17 17 0 0 1 3 4c0-.6.4-1 1-1h3.5c.6 0 1 .4 1 1 0 1.2.2 2.4.6 3.6.1.3 0 .7-.2 1z"/></svg></span>
      <div><small>Call Us Today</small><strong>+41 44 555 0190</strong></div>
    </div>
  </div>
</section>

<section class="services">
  <h2 class="section-title">OUR <b style="font-weight:400">SERVICES</b></h2>
  <div class="title-divider"><span></span><i></i><span></span></div>
  <p class="services-copy">We were also the first to realize that the real estate world was changing, and we needed to change with it to continue innovating. Now we are investors, founders and developers behind some of the most intriguing companies in the business. <a>Contact us</a> to learn more.</p>
  <div class="service-grid">
    <div class="service-card active">
      <div class="service-icon"><svg width="40" height="40" viewBox="0 0 40 40" fill="none" stroke="#fff" stroke-width="2.5"><rect x="14" y="4" width="12" height="9"/><rect x="3" y="27" width="10" height="9"/><rect x="27" y="27" width="10" height="9"/><path d="M20 13v7M8 27v-7h24v7M20 20v7"/></svg></div>
      <h3>Information Management</h3><p>Duis autem vel eum iriure dolor in hendrerit in vulputate</p><span class="plus">−</span>
    </div>
    <div class="service-card">
      <div class="service-icon"><svg width="36" height="36" viewBox="0 0 36 36"><circle cx="18" cy="10" r="7" fill="#fff"/><path d="M4 35c0-9 6-14 14-14s14 5 14 14z" fill="#fff"/></svg></div>
      <h3>Case Support</h3><p>Duis autem vel eum iriure dolor in hendrerit in vulputate</p><span class="plus">+</span>
    </div>
    <div class="service-card">
      <div class="service-icon"><svg width="38" height="38" viewBox="0 0 38 38" fill="none" stroke="#fff" stroke-width="2.5"><rect x="4" y="4" width="30" height="22"/><path d="M12 34h14M19 26v8M11 16l5-5 5 5 6-6"/></svg></div>
      <h3>Application Development</h3><p>Duis autem vel eum iriure dolor in hendrerit in vulputate</p><span class="plus">+</span>
    </div>
    <div class="service-card">
      <div class="service-icon"><svg width="36" height="36" viewBox="0 0 36 36"><path d="M18 2c6 6 8 13 4 20h-8C10 15 12 8 18 2zM4 14c6 0 10 4 11 9-6 0-10-4-11-9zM32 14c-6 0-10 4-11 9 6 0 10-4 11-9zM17 22h2v12h-2z" fill="#fff"/></svg></div>
      <h3>Environmental Litigation</h3><p>Duis autem vel eum iriure dolor in hendrerit in vulputate</p><span class="plus">+</span>
    </div>
    <div class="service-card">
      <div class="service-icon"><svg width="36" height="36" viewBox="0 0 36 36" fill="none" stroke="#fff" stroke-width="3"><circle cx="16" cy="16" r="11"/><circle cx="16" cy="16" r="4"/><path d="M24 24l9 9"/></svg></div>
      <h3>Legal Word Processing</h3><p>Duis autem vel eum iriure dolor in hendrerit in vulputate</p><span class="plus">+</span>
    </div>
    <div class="service-card">
      <div class="service-icon"><svg width="38" height="38" viewBox="0 0 38 38"><circle cx="19" cy="8" r="5" fill="#fff"/><circle cx="7" cy="30" r="5" fill="#fff"/><circle cx="19" cy="30" r="5" fill="#fff"/><circle cx="31" cy="30" r="5" fill="#fff"/><path d="M19 13v12M7 25v-5h24v5" stroke="#fff" stroke-width="2.5" fill="none"/></svg></div>
      <h3>Procurement Support</h3><p>Duis autem vel eum iriure dolor in hendrerit in vulputate</p><span class="plus">+</span>
    </div>
  </div>
</section>

<section class="banner team-banner">
  <div class="photo" role="img" aria-label="Silhouettes of a business team standing before a window over the city at night"></div>
  <div class="banner-box">
    <h2>OUR TEAM</h2>
    <p>eaque ipsa quae ab illo inventore veritatis et quasi architecto beatae vitae dicta sunt explicabo sed ut perspiciatis unde omnis iste natus error sit.</p>
  </div>
</section>

<section class="team">
  <div class="team-list">
    <div class="member"><div class="member-photo" role="img" aria-label="Team member portrait"></div><h3>Lorem Ipsum</h3><div class="member-links"><span><svg width="12" height="12" viewBox="0 0 24 24"><path fill="#1b3a6b" d="M6.6 10.8a15 15 0 0 0 6.6 6.6l2.2-2.2c.3-.3.7-.4 1-.2 1.1.4 2.3.6 3.6.6.6 0 1 .4 1 1V20c0 .6-.4 1-1 1A17 17 0 0 1 3 4c0-.6.4-1 1-1h3.5c.6 0 1 .4 1 1 0 1.2.2 2.4.6 3.6.1.3 0 .7-.2 1z"/></svg></span><span><svg width="12" height="10" viewBox="0 0 24 18"><rect width="24" height="18" fill="#1b3a6b"/><path d="M0 0l12 9 12-9" stroke="#fff" stroke-width="2" fill="none"/></svg></span><span><svg width="12" height="12" viewBox="0 0 24 24" fill="#1b3a6b"><circle cx="18" cy="5" r="4"/><circle cx="6" cy="12" r="4"/><circle cx="18" cy="19" r="4"/><path d="M6 12 18 5M6 12l12 7" stroke="#1b3a6b" stroke-width="2"/></svg></span></div></div>
    <div class="member"><div class="member-photo" role="img" aria-label="Team member portrait"></div><h3>Lorem Ipsum</h3><div class="member-links"><span><svg width="12" height="12" viewBox="0 0 24 24"><path fill="#1b3a6b" d="M6.6 10.8a15 15 0 0 0 6.6 6.6l2.2-2.2c.3-.3.7-.4 1-.2 1.1.4 2.3.6 3.6.6.6 0 1 .4 1 1V20c0 .6-.4 1-1 1A17 17 0 0 1 3 4c0-.6.4-1 1-1h3.5c.6 0 1 .4 1 1 0 1.2.2 2.4.6 3.6.1.3 0 .7-.2 1z"/></svg></span><span><svg width="12" height="10" viewBox="0 0 24 18"><rect width="24" height="18" fill="#1b3a6b"/><path d="M0 0l12 9 12-9" stroke="#fff" stroke-width="2" fill="none"/></svg></span><span><svg width="12" height="12" viewBox="0 0 24 24" fill="#1b3a6b"><circle cx="18" cy="5" r="4"/><circle cx="6" cy="12" r="4"/><circle cx="18" cy="19" r="4"/><path d="M6 12 18 5M6 12l12 7" stroke="#1b3a6b" stroke-width="2"/></svg></span></div></div>
    <div class="member"><div class="member-photo" role="img" aria-label="Team member portrait"></div><h3>Lorem Ipsum</h3><div class="member-links"><span><svg width="12" height="12" viewBox="0 0 24 24"><path fill="#1b3a6b" d="M6.6 10.8a15 15 0 0 0 6.6 6.6l2.2-2.2c.3-.3.7-.4 1-.2 1.1.4 2.3.6 3.6.6.6 0 1 .4 1 1V20c0 .6-.4 1-1 1A17 17 0 0 1 3 4c0-.6.4-1 1-1h3.5c.6 0 1 .4 1 1 0 1.2.2 2.4.6 3.6.1.3 0 .7-.2 1z"/></svg></span><span><svg width="12" height="10" viewBox="0 0 24 18"><rect width="24" height="18" fill="#1b3a6b"/><path d="M0 0l12 9 12-9" stroke="#fff" stroke-width="2" fill="none"/></svg></span><span><svg width="12" height="12" viewBox="0 0 24 24" fill="#1b3a6b"><circle cx="18" cy="5" r="4"/><circle cx="6" cy="12" r="4"/><circle cx="18" cy="19" r="4"/><path d="M6 12 18 5M6 12l12 7" stroke="#1b3a6b" stroke-width="2"/></svg></span></div></div>
    <div class="member"><div class="member-photo" role="img" aria-label="Team member portrait"></div><h3>Lorem Ipsum</h3><div class="member-links"><span><svg width="12" height="12" viewBox="0 0 24 24"><path fill="#1b3a6b" d="M6.6 10.8a15 15 0 0 0 6.6 6.6l2.2-2.2c.3-.3.7-.4 1-.2 1.1.4 2.3.6 3.6.6.6 0 1 .4 1 1V20c0 .6-.4 1-1 1A17 17 0 0 1 3 4c0-.6.4-1 1-1h3.5c.6 0 1 .4 1 1 0 1.2.2 2.4.6 3.6.1.3 0 .7-.2 1z"/></svg></span><span><svg width="12" height="10" viewBox="0 0 24 18"><rect width="24" height="18" fill="#1b3a6b"/><path d="M0 0l12 9 12-9" stroke="#fff" stroke-width="2" fill="none"/></svg></span><span><svg width="12" height="12" viewBox="0 0 24 24" fill="#1b3a6b"><circle cx="18" cy="5" r="4"/><circle cx="6" cy="12" r="4"/><circle cx="18" cy="19" r="4"/><path d="M6 12 18 5M6 12l12 7" stroke="#1b3a6b" stroke-width="2"/></svg></span></div></div>
    <div class="member"><div class="member-photo" role="img" aria-label="Team member portrait"></div><h3>Lorem Ipsum</h3><div class="member-links"><span><svg width="12" height="12" viewBox="0 0 24 24"><path fill="#1b3a6b" d="M6.6 10.8a15 15 0 0 0 6.6 6.6l2.2-2.2c.3-.3.7-.4 1-.2 1.1.4 2.3.6 3.6.6.6 0 1 .4 1 1V20c0 .6-.4 1-1 1A17 17 0 0 1 3 4c0-.6.4-1 1-1h3.5c.6 0 1 .4 1 1 0 1.2.2 2.4.6 3.6.1.3 0 .7-.2 1z"/></svg></span><span><svg width="12" height="10" viewBox="0 0 24 18"><rect width="24" height="18" fill="#1b3a6b"/><path d="M0 0l12 9 12-9" stroke="#fff" stroke-width="2" fill="none"/></svg></span><span><svg width="12" height="12" viewBox="0 0 24 24" fill="#1b3a6b"><circle cx="18" cy="5" r="4"/><circle cx="6" cy="12" r="4"/><circle cx="18" cy="19" r="4"/><path d="M6 12 18 5M6 12l12 7" stroke="#1b3a6b" stroke-width="2"/></svg></span></div></div>
  </div>
</section>

<section class="banner blog-banner">
  <div class="photo" role="img" aria-label="Downtown skyline of glass towers"></div>
  <div class="banner-box">
    <h2>LATEST BLOG POSTS</h2>
    <p>eaque ipsa quae ab illo inventore veritatis et quasi architecto beatae vitae dicta sunt explicabo sed ut perspiciatis unde omnis iste natus error sit voluptatem accusantium doloremque laudantium, totam rem aperiam, eaque.</p>
  </div>
</section>

<section class="blog">
  <div class="post-list">
    <article class="post">
      <div class="post-img" role="img" aria-label="Digital circuit board graphic" style="background:linear-gradient(135deg,#0c3b7a,#2f8fd8)"></div>
      <div class="post-body"><div class="post-date">24<small>APR</small></div><div><h3>Lorem ipsum dolor sit amet,</h3><div class="meta">by admin - in news, business</div><p>Ut wisi enim ad minim veniam, quisnostrud exerci tation ullamcorper.</p></div></div>
    </article>
    <article class="post">
      <div class="post-img" role="img" aria-label="Team hands joining puzzle pieces" style="background:linear-gradient(135deg,#c9cfd8,#7b8798)"></div>
      <div class="post-body"><div class="post-date">24<small>APR</small></div><div><h3>Duis autem vel eum iriure dolo,</h3><div class="meta">by admin - in news, business</div><p>Ut wisi enim ad minim veniam, quisnostrud exerci tation ullamcorper.</p></div></div>
    </article>
    <article class="post">
      <div class="post-img" role="img" aria-label="Office desk with laptop and papers" style="background:linear-gradient(135deg,#e8e2d6,#a89a86)"></div>
      <div class="post-body"><div class="post-date">24<small>APR</small></div><div><h3>Vel illum dolore eu feugiat nulla</h3><div class="meta">by admin - in news, business</div><p>Ut wisi enim ad minim veniam, quisnostrud exerci tation ullamcorper.</p></div></div>
    </article>
  </div>
  <div class="dots"><span></span><span></span><span></span><span></span></div>
</section>

<section class="callback">
  <h2>Request<br>A Call Back.</h2>
  <p class="callback-copy">Duis autem vel eum iriure dolor in hendrerit in vulputate velit esse molestie consequat, vel illum dolore eu feugiat nulla facilisis at vero eros ... [+]</p>
  <div class="callback-form">
    <h3>Please fill up bellow form</h3>
    <div class="form-grid">
      <div class="field">Name</div><div class="field">Email</div>
      <div class="field">Phone</div><div class="field">Message</div>
    </div>
    <span class="btn-submit">SUBMIT</span>
  </div>
</section>

<footer class="site-footer">
  <div class="contact-row">
    <div class="contact-item"><div class="ico"><svg width="20" height="28" viewBox="0 0 20 28"><path d="M10 1a9 9 0 0 0-9 9c0 7 9 17 9 17s9-10 9-17a9 9 0 0 0-9-9z" fill="none" stroke="#fff" stroke-width="2"/><circle cx="10" cy="10" r="3" fill="#fff"/></svg></div>52 Lorem ipsum dolor 456 Sed diam, nonummy</div>
    <div class="contact-item"><div class="ico"><svg width="26" height="26" viewBox="0 0 24 24"><path fill="none" stroke="#fff" stroke-width="1.6" d="M6.6 10.8a15 15 0 0 0 6.6 6.6l2.2-2.2c.3-.3.7-.4 1-.2 1.1.4 2.3.6 3.6.6.6 0 1 .4 1 1V20c0 .6-.4 1-1 1A17 17 0 0 1 3 4c0-.6.4-1 1-1h3.5c.6 0 1 .4 1 1 0 1.2.2 2.4.6 3.6.1.3 0 .7-.2 1z"/></svg></div>Phone: (044) 555-0190</div>
    <div class="contact-item"><div class="ico"><svg width="26" height="26" viewBox="0 0 26 26"><path d="M2 12 24 2 16 24l-3-9z M13 15 24 2" fill="none" stroke="#fff" stroke-width="1.8"/></svg></div>Email: info@kova.com</div>
  </div>
  <div class="footer-brand">KOVA</div>
  <p class="footer-copy">Lorem ipsum dolor sit amet, consectetuer adipiscing elit, sed diam nonummy nibh euismod tincidunt ut laoreet dolore magna aliquam.</p>
  <div class="hours"><span>MON - FRI: 8:00 - 17:00</span><span>SATURDAY: 9:00 - 15:00</span><span>SUNDAY: CLOSED</span></div>
  <span class="btn-contact">CONTACT US</span>
</footer>

<div class="copyright" style="position:absolute;left:0;width:1200px">
  <span>Copyright © 2017 KOVA . All Right Reserved.</span>
  <div class="social"><span></span><span></span><span></span><span></span></div>
</div>

</body>
</html>
```